Simple landing page for Brambles cookbook

I need a one page landingpage where customers can order the cookbook.
This is a cookbook of a collection of recipes from our deli that we used to run.
I need a landing page where customers can come and order the book. I also need it coded. I already have the domain through hostwell.
I can send the file of the book through wetransfer. It's too big to upload here. Just so you get the feel that I am looking for.
I attached a simple text as an introduction to the page. But I am open to any suggestions. I want it all to be about the experience that we are sharing the recipes with everybody and that it's for sale. The book is $29.99, shipping included.
Customers have to be able to click and buy the book from it.

Coding

Coded - Design and coding required

Number of Pages Required

1 page

Font styles to use
Sans Serif

Requirements
Must have
• Same colors as the cookbook

```html
<!DOCTYPE html>
<html lang="en">
<head>
<meta charset="utf-8">
<title>Brambles Sandwiches Cookbook</title>
<link href="https://fonts.googleapis.com/css2?family=Bebas+Neue&family=Quicksand:wght@500;600;700&display=swap" rel="stylesheet">
<style>
:root{
  --brown:#4a2a1c;
  --crimson:#c41e55;
  --crimson-dark:#a8174a;
  --blue:#2f86b8;
  --blue-deep:#1f5578;
  --sky:#c6def0;
  --sky-light:#e3eff8;
  --green:#7c9b34;
  --white:#ffffff;
  --ink:#1f1f1f;
}
*{margin:0;padding:0;box-sizing:border-box}
html,body{width:1200px;height:2513px;overflow:hidden;background:var(--white)}
body{position:relative;font-family:'Quicksand',sans-serif;color:var(--ink)}
.abs{position:absolute}
.waves{position:absolute;left:0;width:1200px}
.brand{font-family:'Bebas Neue',sans-serif;color:var(--brown);font-size:44px;line-height:36px;letter-spacing:1px}
.brand small{display:block;font-size:25px;line-height:24px;letter-spacing:.5px}
.hero-title{left:145px;top:205px;width:520px;font-family:'Bebas Neue',sans-serif;font-size:43px;line-height:51px;letter-spacing:1.5px;color:var(--brown)}
.includes{left:145px;top:380px;font-size:16px;font-weight:700;letter-spacing:1.5px;color:var(--brown)}
.includes strong{color:var(--crimson);font-size:22px;letter-spacing:1.5px}
.categories{left:145px;top:415px;display:flex;gap:30px;font-size:14px;font-weight:600;letter-spacing:.8px}
.categories span{display:flex;align-items:center;gap:8px}
.btn{position:absolute;display:flex;align-items:center;justify-content:center;width:152px;height:37px;border-radius:19px;background:var(--crimson);color:var(--white);font-family:'Bebas Neue',sans-serif;font-size:19px;letter-spacing:2px;text-decoration:none}
.book-cover{left:722px;top:50px;width:345px;height:505px;border-radius:4px 14px 14px 4px;background:linear-gradient(160deg,#f4f6f8 0%,#e8ecef 35%,#c9a06a 55%,#9c6a3c 70%,#d8dde2 100%);box-shadow:10px 12px 30px rgba(60,80,110,.25)}
.price-badge{position:absolute}
.feature-card{left:145px;top:738px;width:910px;height:517px;border-radius:12px;overflow:hidden;box-shadow:0 20px 50px rgba(40,60,90,.18);display:flex}
.feature-photo{width:458px;height:100%;background:linear-gradient(135deg,#6f8f4a 0%,#d8b872 40%,#f1e3b8 60%,#5a3b26 100%)}
.feature-text{flex:1;background:linear-gradient(180deg,var(--blue) 0%,var(--blue-deep) 100%);position:relative}
.feature-text p{position:absolute;left:58px;top:118px;width:360px;font-family:'Bebas Neue',sans-serif;font-size:27px;line-height:41px;letter-spacing:2px;color:var(--white)}
.seal{left:536px;top:703px;width:136px;height:136px;border-radius:50%;background:var(--white);border:6px solid var(--green);display:flex;align-items:center;justify-content:center;text-align:center;font-family:'Quicksand',sans-serif;font-weight:700;font-size:25px;line-height:26px;letter-spacing:1.5px;color:var(--ink);box-shadow:0 6px 18px rgba(0,0,0,.12)}
.books-stack{left:0;top:1425px;width:665px;height:435px;background:linear-gradient(135deg,#dfe8f0 0%,#b9cbd9 40%,#a87948 60%,#c9d6e1 100%);clip-path:polygon(0 15%,38% 0%,100% 52%,70% 100%,0 80%)}
.offer-title{left:600px;top:1550px;width:495px;text-align:center;font-family:'Bebas Neue',sans-serif;font-size:54px;line-height:51px;letter-spacing:3px;color:var(--brown)}
.offer-sub{left:600px;top:1665px;width:495px;text-align:center;font-size:14px;font-weight:600;line-height:19px;letter-spacing:1px;color:var(--ink)}
.pretzel-photo{left:300px;top:1935px;width:900px;height:495px;background:radial-gradient(ellipse at 52% 48%,#b5641f 0%,#c98a3c 30%,#e9c98a 48%,rgba(240,232,222,.6) 70%,rgba(255,255,255,0) 88%)}
.quote-card{left:145px;top:2080px;width:438px;height:235px;background:var(--white);border-radius:0 14px 14px 14px;border-left:5px solid var(--blue);border-bottom:5px solid var(--blue-deep);box-shadow:0 10px 30px rgba(0,0,0,.08)}
.quote-card p{position:absolute;left:27px;top:48px;width:390px;font-size:19px;line-height:29.5px;font-weight:500;letter-spacing:1px}
.quote-mark{left:157px;top:2048px;width:61px;height:61px;border-radius:50%;background:var(--crimson);display:flex;align-items:center;justify-content:center;color:var(--white);font-size:42px;font-weight:700;padding-top:14px}
.footer{left:145px;top:2417px;width:910px;height:71px;border-radius:12px;background:linear-gradient(180deg,var(--blue) 0%,var(--blue-deep) 100%);display:flex;align-items:center;justify-content:center;color:var(--white);font-size:14px;font-weight:600;letter-spacing:.5px}
</style>
</head>
<body>

<!-- Hero -->
<svg class="waves" style="top:0" height="620" viewBox="0 0 1200 620" aria-hidden="true">
  <defs>
    <linearGradient id="heroSky" x1="0" y1="0" x2="1" y2="0">
      <stop offset="0" stop-color="#bcd8ee"/>
      <stop offset=".6" stop-color="#dbe9f5"/>
      <stop offset="1" stop-color="#cfe2f1"/>
    </linearGradient>
    <radialGradient id="heroGlow" cx=".25" cy=".55" r=".45">
      <stop offset="0" stop-color="#fff" stop-opacity=".95"/>
      <stop offset="1" stop-color="#fff" stop-opacity="0"/>
    </radialGradient>
  </defs>
  <path d="M0 200 C200 120 420 110 640 190 C850 260 1020 290 1200 250 L1200 620 L0 620 Z" fill="url(#heroSky)" opacity=".8"/>
  <path d="M80 220 C240 130 420 120 620 170 C430 130 260 150 80 220 Z" fill="#fff" opacity=".8"/>
  <path d="M0 520 C300 460 700 470 1200 560 L1200 620 L0 620 Z" fill="#fff"/>
  <rect width="1200" height="620" fill="url(#heroGlow)"/>
</svg>

<div class="abs brand" style="left:147px;top:33px">Brambles<small>Sandwiches</small></div>

<h1 class="abs hero-title">It's finally here! The Brambles cookbook with all your favourite recipes</h1>
<div class="abs includes">BOOK INCLUDES <strong>28 RECIPES</strong>:</div>
<div class="abs categories">
  <span><svg width="20" height="14" viewBox="0 0 20 14" aria-hidden="true"><path d="M2 8 Q10 0 18 8 Z M2 10 H18 M3 12 H17" fill="none" stroke="#9aa56a" stroke-width="1.5"/></svg>Sandwiches</span>
  <span><svg width="20" height="14" viewBox="0 0 20 14" aria-hidden="true"><path d="M1 5 H19 Q17 12 10 12 Q3 12 1 5 Z" fill="none" stroke="#9aa56a" stroke-width="1.5"/></svg>Sauces</span>
  <span><svg width="20" height="16" viewBox="0 0 20 16" aria-hidden="true"><path d="M2 8 Q10 0 18 8 Z M2 10 H18 M3 13 H17" fill="none" stroke="#9aa56a" stroke-width="1.5"/></svg>Burgers</span>
</div>
<a class="btn" href="#order" style="left:145px;top:467px">Order now</a>

<div class="abs book-cover" role="img" aria-label="Brambles Sandwiches cookbook cover with a stacked sandwich photo"></div>

<svg class="price-badge" style="left:648px;top:126px" width="150" height="150" viewBox="0 0 150 150" aria-label="$29.99 free shipping">
  <defs><radialGradient id="badgeGlow"><stop offset=".5" stop-color="#c41e55" stop-opacity=".35"/><stop offset="1" stop-color="#c41e55" stop-opacity="0"/></radialGradient></defs>
  <circle cx="75" cy="75" r="75" fill="url(#badgeGlow)"/>
  <path d="M75 8 L88 20 L106 16 L112 33 L130 39 L126 57 L138 72 L126 87 L130 105 L112 111 L106 128 L88 124 L75 136 L62 124 L44 128 L38 111 L20 105 L24 87 L12 72 L24 57 L20 39 L38 33 L44 16 L62 20 Z" fill="#c41e55" stroke="#c41e55" stroke-width="6" stroke-linejoin="round"/>
  <text x="20" y="80" font-family="Bebas Neue, sans-serif" font-size="18" fill="#fff">$</text>
  <text x="31" y="84" font-family="Bebas Neue, sans-serif" font-size="42" letter-spacing="1" fill="#fff">29.99</text>
  <rect x="33" y="96" width="18" height="12" rx="2" fill="none" stroke="#fff" stroke-width="1.5"/>
  <text x="56" y="101" font-family="Quicksand, sans-serif" font-size="10" font-weight="600" fill="#fff">Free</text>
  <text x="56" y="113" font-family="Quicksand, sans-serif" font-size="10" font-weight="600" fill="#fff">Shipping</text>
</svg>

<!-- Feature -->
<svg class="waves" style="top:1195px" height="680" viewBox="0 0 1200 680" aria-hidden="true">
  <path d="M0 40 C120 190 360 290 620 300 C850 310 1050 260 1200 190 L1200 650 C1050 660 980 650 920 650 C1000 630 1100 620 1200 600 L1200 650 L0 650 Z" fill="#c6def0"/>
  <path d="M0 40 C120 190 360 290 620 300 C850 310 1050 260 1200 190 L1200 600 C1000 620 820 620 620 590 C400 560 200 540 0 560 Z" fill="#d2e5f3"/>
  <path d="M600 590 C800 640 1000 640 1200 600 L1200 650 L920 650 C1000 630 800 620 600 590 Z" fill="#fff" opacity=".7"/>
</svg>

<div class="abs feature-card">
  <div class="feature-photo" role="img" aria-label="Grilled panini with melted cheese being pulled apart"></div>
  <div class="feature-text">
    <p>We can't open another Brambles restaurant, but we can offer you this compilation of our best recipes for you to make and enjoy at home!</p>
    <a class="btn" href="#order" style="left:54px;top:398px">Byu now</a>
  </div>
</div>
<div class="abs seal">fresh<br>&amp;<br>tasty</div>

<!-- Offer -->
<div class="abs books-stack" role="img" aria-label="Two copies of the Brambles Sandwiches cookbook lying at an angle"></div>

<svg class="price-badge" style="left:790px;top:1430px" width="115" height="115" viewBox="0 0 150 150" aria-label="$29.99 free shipping">
  <defs><radialGradient id="badgeGlow2"><stop offset=".5" stop-color="#c41e55" stop-opacity=".35"/><stop offset="1" stop-color="#c41e55" stop-opacity="0"/></radialGradient></defs>
  <circle cx="75" cy="75" r="75" fill="url(#badgeGlow2)"/>
  <path d="M75 8 L88 20 L106 16 L112 33 L130 39 L126 57 L138 72 L126 87 L130 105 L112 111 L106 128 L88 124 L75 136 L62 124 L44 128 L38 111 L20 105 L24 87 L12 72 L24 57 L20 39 L38 33 L44 16 L62 20 Z" fill="#c41e55" stroke="#c41e55" stroke-width="6" stroke-linejoin="round"/>
  <text x="20" y="80" font-family="Bebas Neue, sans-serif" font-size="18" fill="#fff">$</text>
  <text x="31" y="84" font-family="Bebas Neue, sans-serif" font-size="42" letter-spacing="1" fill="#fff">29.99</text>
  <rect x="33" y="96" width="18" height="12" rx="2" fill="none" stroke="#fff" stroke-width="1.5"/>
  <text x="56" y="101" font-family="Quicksand, sans-serif" font-size="10" font-weight="600" fill="#fff">Free</text>
  <text x="56" y="113" font-family="Quicksand, sans-serif" font-size="10" font-weight="600" fill="#fff">Shipping</text>
</svg>

<h2 class="abs offer-title">Favorite recipes<br>in one book</h2>
<p class="abs offer-sub">We Truly Hope You Will Enjoy Making These<br>Sandwiches Just As Much As We Did.</p>
<a class="btn" id="order" href="#order" style="left:772px;top:1728px">Byu now</a>

<!-- Story -->
<div class="abs pretzel-photo" role="img" aria-label="Salted pretzel sandwich with cheese on a white plate"></div>
<div class="abs brand" style="left:147px;top:1951px">Brambles<small>Sandwiches</small></div>

<div class="abs quote-card">
  <p>We can't open another BRAMBLES, but we can offer you this collection of our recipes for you to try out at home with your family and friends.</p>
</div>
<div class="abs quote-mark">&#8221;</div>

<footer class="abs footer">Copyright 2022. Marlene Voss | All Rights Reserved</footer>

</body>
</html>
```